A specialised Sport management needs a corporate brochure design

We are a specialized company in the management and consultancy of sports events. and need to have a company brochure
We provide the following services;
Event management
Venues management
Production
Ticketing
Consulting
Hospitality
Activity management
Event timing
Branding of event
Event supplies
We need a corporate profile design for our company to showcase the major events that we have covered , with images, information, statistics, surveys, products and services used. We want to highlight our professionalism and execution of the events, experience of the participants, spectators . How we have grown in the past few years and reached the international standards.
Objectives of the work:
To get sponsors and partners for future business and to present Tri-Crest
as not just a sports management company but also a professional sports
events management company.
You can check our website
www.tri-crest.example
Target Market(s)
Sponsors and corporate partners
Industry/Entity Type
Events
Requirements
Must have
- Must Have:
- - Very professional look
- -Some event images,Event information, statistics, surveys, products and services used. We want to highlight our professionalism and execution of the events (Attached)
Nice to have
- Similar momentom of the below design
- http://www.lumavent.example/wp-content/themes/lumavent/pdf/CP-2014-15-V10-Web.pdf

```html
<!DOCTYPE html>
<html lang="en">
<head>
<meta charset="utf-8">
<title>Tri-Crest Sport Management – Brochure Cover</title>
<link rel="stylesheet" href="https://fonts.googleapis.com/css2?family=Oswald:wght@200;300;600&family=Barlow:wght@400;600&display=swap">
<style>
  :root {
    --page-dark: #231f20;
    --page-edge: #3a3637;
    --card-white: #ffffff;
    --ink: #231f20;
    --rule: #c9c9c9;
    --accent-orange: #ef5a24;
    --accent-green: #1b7a3e;
    --accent-grey: #8a8a8a;
    --headline: #ffffff;
  }
  html, body {
    margin: 0;
    padding: 0;
    overflow: hidden;
    background: var(--page-dark);
  }
  .spread {
    position: relative;
    width: 1200px;
    height: 601px;
    overflow: hidden;
    background: var(--page-dark);
  }
  .page {
    position: absolute;
    top: 0;
    width: 600px;
    height: 601px;
    background: var(--page-dark);
  }
  .page--back { left: 0; }
  .page--front { left: 600px; border-left: 1px solid var(--page-edge); box-sizing: border-box; }

  /* Contact card on back page */
  .contact-card {
    position: absolute;
    left: 2px;
    top: 385px;
    width: 177px;
    height: 190px;
    background: var(--card-white);
    font-family: "Barlow", Arial, sans-serif;
    color: var(--ink);
  }
  .brand {
    position: absolute;
    left: 0;
    top: 18px;
    width: 177px;
    text-align: center;
  }
  .brand__name {
    display: inline-flex;
    align-items: center;
    gap: 6px;
    font-family: "Oswald", Arial, sans-serif;
    font-weight: 600;
    font-size: 22px;
    letter-spacing: 0.5px;
    color: var(--ink);
  }
  .brand__dot {
    width: 12px;
    height: 12px;
    border-radius: 50%;
    background: var(--accent-green);
  }
  .brand__tagline {
    display: block;
    margin-top: 4px;
    font-size: 8px;
    letter-spacing: 1.2px;
    color: var(--accent-grey);
  }
  .contact-card__rule {
    position: absolute;
    left: 56px;
    top: 96px;
    width: 115px;
    height: 1px;
    background: var(--rule);
  }
  .contact-list {
    position: absolute;
    left: 59px;
    top: 106px;
    margin: 0;
    padding: 0;
    list-style: none;
    font-size: 10.5px;
    line-height: 12px;
  }
  .contact-list li {
    display: flex;
    align-items: center;
    gap: 3px;
  }
  .contact-list li.gap-before { margin-top: 6px; }
  .contact-list li + li { margin-top: 5px; }
  .contact-list li.tight { margin-top: 0; }
  .contact-icon {
    width: 8px;
    height: 8px;
    flex: none;
  }

  /* Front page ring */
  .ring {
    position: absolute;
    left: 0;
    top: 0;
    width: 600px;
    height: 601px;
  }
  .headline {
    position: absolute;
    left: 140px;
    top: 237px;
    margin: 0;
    font-family: "Oswald", "Arial Narrow", sans-serif;
    font-weight: 200;
    font-size: 43px;
    line-height: 52px;
    letter-spacing: 0.5px;
    color: var(--headline);
    text-transform: uppercase;
  }
</style>
</head>
<body>
<main class="spread">

  <section class="page page--back">
    <aside class="contact-card">
      <div class="brand">
        <span class="brand__name"><span class="brand__dot"></span>TRI-CREST</span>
        <span class="brand__tagline">SPORT MANAGEMENT</span>
      </div>
      <div class="contact-card__rule"></div>
      <ul class="contact-list">
        <li><svg class="contact-icon" viewBox="0 0 8 8"><circle cx="4" cy="4" r="4" fill="#4a90c8"/></svg>555 0142 7731</li>
        <li><svg class="contact-icon" viewBox="0 0 8 8"><circle cx="4" cy="4" r="4" fill="#4a90c8"/></svg>555 0186 2209</li>
        <li class="gap-before"><svg class="contact-icon" viewBox="0 0 8 8"><circle cx="4" cy="4" r="4" fill="#4a90c8"/></svg>events@tri-crest.example</li>
        <li class="tight"><svg class="contact-icon" viewBox="0 0 8 8"><circle cx="4" cy="4" r="4" fill="#4a90c8"/></svg>www.tri-crest.example</li>
        <li class="tight"><svg class="contact-icon" viewBox="0 0 8 8"><circle cx="4" cy="4" r="4" fill="#4a90c8"/></svg>TCsportevents</li>
      </ul>
    </aside>
  </section>

  <section class="page page--front">
    <svg class="ring" viewBox="575 0 574 575" preserveAspectRatio="none" aria-hidden="false">
      <defs>
        <clipPath id="ring-outer">
          <circle cx="915" cy="305" r="226"/>
        </clipPath>
        <linearGradient id="tone-runners" x1="0" y1="0" x2="0" y2="1">
          <stop offset="0" stop-color="#b9d3e6"/>
          <stop offset="0.35" stop-color="#c9b79a"/>
          <stop offset="1" stop-color="#4b4a47"/>
        </linearGradient>
        <linearGradient id="tone-collage" x1="0" y1="0" x2="0" y2="1">
          <stop offset="0" stop-color="#9a8f86"/>
          <stop offset="0.4" stop-color="#7f9fb4"/>
          <stop offset="0.7" stop-color="#a7873e"/>
          <stop offset="1" stop-color="#6e5a52"/>
        </linearGradient>
        <linearGradient id="tone-swimmers" x1="0" y1="0" x2="0" y2="1">
          <stop offset="0" stop-color="#a9c9e3"/>
          <stop offset="0.45" stop-color="#6f6a5f"/>
          <stop offset="1" stop-color="#6e9fc0"/>
        </linearGradient>
      </defs>
      <g clip-path="url(#ring-outer)">
        <polygon role="img" aria-label="Photo: crowd of marathon runners on a sunny seaside road"
          points="680,60 1160,60 1060,135 975,205 880,298 690,110" fill="url(#tone-runners)"/>
        <polygon role="img" aria-label="Photo collage: climbing, flags, trail running, team sports and race finish scenes"
          points="1066,138 1160,60 1160,560 1050,450 1000,392 880,298 975,207" fill="url(#tone-collage)"/>
        <polygon role="img" aria-label="Photo: triathlon swimmers running into the sea at the start"
          points="997,395 1048,455 1160,560 680,560 715,470 880,298" fill="url(#tone-swimmers)"/>
      </g>
      <!-- gaps between segments -->
      <line x1="1070" y1="128" x2="968" y2="212" stroke="var(--page-dark)" stroke-width="7"/>
      <line x1="992" y1="388" x2="1058" y2="462" stroke="var(--page-dark)" stroke-width="7"/>
      <!-- ring opening and centre -->
      <polygon points="880,300 712,120 640,120 640,480 716,466" fill="var(--page-dark)"/>
      <circle cx="878" cy="298" r="128" fill="var(--page-dark)"/>
    </svg>
    <h1 class="headline">Let's take care of<br>your next<br>sports event!</h1>
  </section>

</main>
</body>
</html>
```